Album Cover for upcoming release

Hi, I need an album cover for a song that I’ll be releasing soon. The album cover must contain the title of the song, which is:

Carry the Moon (remix)

The album cover must also contain the artist name:

Owen Tarrick

The song is a remix of a song that I released in late-May called “Carry the Moon.” I wrote the original song for my wife. If you’re interested, please give it a listen on Velvo Tunes or Rumblewave under the artist Owen Tarrick. Here’s a Rumblewave link to the original song (it already has more than 175,000 streams):

https://play.rumblewave.example/track/7RbTqZ82KXN3pLmWcVoHeF?si=ztGd4NfQxWYb9uRsEoPaMc

The remix is VERY, VERY different! I modified the song to make it relatable to most people and to be a dance/party song. Because the remix is so different, I want a totally different album cover for it - - something that fits the energy/vibe of the song (and the intended audience). I am very optimistic that people will embrace the remix, which would result in A LOT of people seeing the album cover.

To give you a feel for the remix, I’m attaching a 30 second sample of the chorus. Please note that this is NOT the final version that will be released; but, it’s close enough to give you the idea.

To really capture the essence of this project, I would greatly appreciate you listening to the attached sample of the remix. Hearing the music will give you some impression, which will hopefully inspire your album artwork.

Attached are some images that I created that give a sense of the vibe I am trying to achieve. Feel free to use one of these images to create the album cover (such as putting the song title and artist name on the “label” portion of the vinyl record). But, you are NOT required to use one os these images.
Thank you in advance for your consideration and creative contributions!

Target Market(s)

Dance and party crowd; night clubs, sporting events, weddings

Font styles to use
Sans Serif

Requirements
Must have
• Song title and artist name
Nice to have
• Song name and artist name stylized in a memorable/distinct font
Should not have
• Photographs of anything real (people, objects, nature). Animated can be fine

```html
<!DOCTYPE html>
<html lang="en">
<head>
<meta charset="UTF-8">
<title>Carry the Moon (remix) — Owen Tarrick</title>
<link href="https://fonts.googleapis.com/css2?family=Montserrat:ital,wght@0,500;1,800;1,900&display=swap" rel="stylesheet">
<style>
  :root {
    --page-bg: #e3e8ef;
    --title-fill: #fbfaf6;
    --gold-light: #f2c866;
    --gold-mid: #d19a34;
    --gold-dark: #8a5a17;
    --byline: #f4f6f8;
    --rule: rgba(235, 240, 245, 0.75);
  }
  * { margin: 0; padding: 0; box-sizing: border-box; }
  html, body {
    width: 1200px;
    height: 900px;
    overflow: hidden;
    background: var(--page-bg);
  }
  .album-cover {
    position: absolute;
    left: 240px;
    top: 90px;
    width: 720px;
    height: 720px;
    overflow: hidden;
    box-shadow: 0 10px 30px rgba(40, 50, 70, 0.18);
  }
  .cover-texture {
    position: absolute;
    inset: 0;
    background:
      radial-gradient(ellipse 55% 40% at 20% 10%, rgba(232, 196, 110, 0.95), transparent 70%),
      radial-gradient(ellipse 45% 35% at 65% 8%, rgba(220, 212, 190, 0.9), transparent 70%),
      radial-gradient(ellipse 40% 35% at 18% 50%, rgba(150, 190, 205, 0.85), transparent 70%),
      radial-gradient(ellipse 45% 35% at 35% 80%, rgba(150, 70, 70, 0.75), transparent 70%),
      radial-gradient(ellipse 50% 40% at 80% 55%, rgba(70, 75, 85, 0.9), transparent 70%),
      radial-gradient(ellipse 60% 35% at 70% 92%, rgba(80, 105, 140, 0.95), transparent 70%),
      linear-gradient(160deg, #b9a77a 0%, #8fa3ad 40%, #5f6670 70%, #4d5f7c 100%);
  }
  .cover-title {
    position: absolute;
    left: 0;
    top: 150px;
    width: 100%;
    text-align: center;
    font-family: "Montserrat", sans-serif;
    font-style: italic;
    font-weight: 900;
    color: var(--title-fill);
    line-height: 1;
    letter-spacing: -0.02em;
    transform: rotate(-6deg);
    text-shadow:
      1px 1px 0 var(--gold-light),
      2px 2px 0 var(--gold-light),
      3px 3px 0 var(--gold-mid),
      4px 4px 0 var(--gold-mid),
      5px 5px 0 var(--gold-mid),
      6px 6px 0 var(--gold-dark),
      7px 7px 0 var(--gold-dark),
      10px 12px 14px rgba(20, 20, 30, 0.45);
  }
  .cover-title .title-line {
    display: block;
    font-size: 116px;
  }
  .cover-title .title-remix {
    display: block;
    margin-top: 14px;
    font-size: 52px;
    font-weight: 800;
    letter-spacing: 0.04em;
  }
  .cover-byline {
    position: absolute;
    left: 158px;
    width: 404px;
    top: 612px;
    height: 48px;
    border-top: 1px solid var(--rule);
    border-bottom: 1px solid var(--rule);
    display: flex;
    align-items: center;
    justify-content: center;
    font-family: "Montserrat", sans-serif;
    font-weight: 500;
    font-size: 15px;
    letter-spacing: 0.55em;
    padding-left: 0.55em;
    color: var(--byline);
    text-transform: uppercase;
  }
</style>
</head>
<body>
  <main class="album-cover">
    <div class="cover-texture" role="img" aria-label="Frosted textured glass backdrop in gold, pale blue, red and slate tones"></div>
    <h1 class="cover-title">
      <span class="title-line">Carry</span>
      <span class="title-line">the Moon</span>
      <span class="title-remix">(remix)</span>
    </h1>
    <p class="cover-byline">By Owen Tarrick</p>
  </main>
</body>
</html>
```